Restaurant Menu New Design

Hello Designers,

Blue Fern is a casual family oriented dine-in restaurant, we serve American Italian dishes like Pizza, Pasta, and Sandwiches.

We are excited about adding some new delicious dishes and recipes to our menu. And we are looking for a talented and creative designer to design it.

The menu is a 12 page black leather book, page size is:
6.5" X 11.69" (16.51 cm X 29.69 cm)

Below is the scope of work and requirements:

1) Design a completely all new, creative, and beautiful menu, including cover page, blue fern oven intro. page, interior pages, and kids menu page.

2) Design a take out edition of the menu. It will be exactly the same as the dine-in menu, but with the addition of a back cover page with info such as contacts, social media, location map, etc…

3) Files are required in Adobe Illustrator format. Layers should be organized, all text should be editable, and all the food pictures easy to change.

4) This is a two language menu, so you are required to make space in the design for a second language. The easiest way to do that is have every item listed in English twice, then I will edit the second text with Illustrator.

5) In your initial design submission, the minimum you are required to submit are these 4 pages:
– Cover page
– Typical interior menu page
– Kids menu page
– Take-out menu back cover page

If your initial design is selected, then you are required to submit all remaining pages to complete the project.

In the link below, you will find:
1) Logo
2) New menu text in Excel
3) Food images (will take some time to upload)
4) The old dine-in and take out menu designs

https://www.filevaultra.com/sh/kq7tmwzabe3pxd/BBBrTnpLk41QaWmZpQ8V2X7Jd?dl=0

Thank you for stopping by and reading this brief. I hope you like this project and enjoy designing our new menu. Please let me know if you have any questions.

Cheers!

Project Deadline Extended
Reason: We have decided to extend the deadline due to the low number of submissions which was much lower than the expected submissions we were give by Brief Harbor.

```html
<!DOCTYPE html>
<html lang="en">
<head>
<meta charset="utf-8">
<title>Blue Fern — Turnovers</title>
<link rel="stylesheet" href="https://fonts.googleapis.com/css2?family=Lato:wght@400;700;900&family=Tajawal:wght@400;500&display=swap">
<style>
  :root {
    --board: #333333;
    --ink: #ffffff;
    --muted: #a4a4a4;
    --rule: #e9e9e9;
    --photo-warm: #b8743a;
    --photo-deep: #6e3a1c;
    --doodle-area: #383838;
  }
  * { margin: 0; padding: 0; box-sizing: border-box; }
  html, body { width: 1200px; height: 2174px; overflow: hidden; background: var(--board); }
  .menu-page {
    position: relative; width: 1200px; height: 2174px; background: var(--board);
    font-family: "Lato", "Helvetica Neue", Arial, sans-serif; color: var(--ink);
  }
  .section-title {
    position: absolute; top: 74px; font-size: 38px; font-weight: 400; letter-spacing: 0.3px;
  }
  .frame-lines { position: absolute; inset: 0; width: 1200px; height: 2174px; pointer-events: none; }
  .food-photo {
    position: absolute;
    background: linear-gradient(135deg, var(--photo-deep), var(--photo-warm) 55%, #e0b26a);
  }
  .doodle-area { position: absolute; background: var(--doodle-area); border-radius: 8px; }
  .menu-item { position: absolute; text-align: center; }
  .item-name { font-size: 26px; font-weight: 900; line-height: 1.25; }
  .item-name .ar { font-family: "Tajawal", "Lato", sans-serif; font-weight: 500; }
  .item-desc {
    margin-top: 24px; font-size: 17px; line-height: 1.35; color: var(--muted);
  }
  .item-desc-ar {
    margin-top: 18px; font-family: "Tajawal", "Lato", sans-serif; direction: rtl;
    font-size: 17px; line-height: 1.35; color: var(--muted);
  }
</style>
</head>
<body>
<main class="menu-page">

  <svg class="frame-lines" viewBox="0 0 1200 2174" fill="none" stroke="var(--rule)" stroke-width="2.2">
    <line x1="0" y1="133" x2="319" y2="133"/>
    <line x1="901" y1="130" x2="1200" y2="130"/>
    <line x1="72" y1="280" x2="225" y2="280"/>
    <line x1="333" y1="280" x2="804" y2="280"/>
    <line x1="72" y1="280" x2="72" y2="587"/>
    <line x1="640" y1="322" x2="640" y2="470"/>
    <line x1="1123" y1="374" x2="1123" y2="626"/>
    <line x1="1014" y1="626" x2="1123" y2="626"/>
    <line x1="0" y1="869" x2="470" y2="869"/>
    <line x1="750" y1="869" x2="1200" y2="869"/>
    <line x1="837" y1="935" x2="1130" y2="935"/>
    <line x1="1130" y1="935" x2="1130" y2="1246"/>
    <line x1="1000" y1="953" x2="1069" y2="953"/>
    <line x1="1069" y1="953" x2="1069" y2="968"/>
    <line x1="656" y1="1569" x2="656" y2="1891"/>
    <line x1="656" y1="1891" x2="956" y2="1891"/>
    <line x1="0" y1="2040" x2="470" y2="2040"/>
    <line x1="750" y1="2040" x2="1200" y2="2040"/>
  </svg>

  <h1 class="section-title" style="left:225px;">TURNOVERS</h1>
  <h1 class="section-title" style="left:768px;">TURNOVERS</h1>

  <div class="doodle-area" role="img" aria-label="Serving cloche line drawing" style="left:532px;top:92px;width:136px;height:98px;"></div>
  <div class="doodle-area" role="img" aria-label="Line drawings of tomato, onion and bell pepper" style="left:238px;top:156px;width:175px;height:56px;"></div>
  <div class="doodle-area" role="img" aria-label="Line drawings of pea pod, lemon slice and mushrooms" style="left:766px;top:152px;width:236px;height:58px;"></div>

  <div class="food-photo" role="img" aria-label="Photo of a spinach feta turnover with fries and coleslaw" style="left:104px;top:316px;width:432px;height:285px;"></div>

  <div class="doodle-area" role="img" aria-label="Line drawing of a spring onion" style="left:558px;top:356px;width:62px;height:90px;"></div>
  <div class="doodle-area" role="img" aria-label="Line drawing of a tomato" style="left:574px;top:538px;width:56px;height:58px;"></div>
  <div class="doodle-area" role="img" aria-label="Line drawing of chili peppers" style="left:552px;top:688px;width:100px;height:80px;"></div>
  <div class="doodle-area" role="img" aria-label="Line drawings of mushrooms and a beetroot" style="left:782px;top:644px;width:235px;height:110px;"></div>

  <div class="doodle-area" role="img" aria-label="Rolling pin ornament on the divider line" style="left:468px;top:846px;width:284px;height:46px;"></div>

  <article class="menu-item" style="left:660px;top:336px;width:450px;">
    <h2 class="item-name">JAMAICAN CHICKEN<br><span class="ar">| دجاج جاميكان</span></h2>
    <p class="item-desc">Jamican style grilled chicken breast, red onios,<br>green bell peppers, and white cheddar cheese<br>37</p>
    <p class="item-desc-ar">شرائح دجاج مع التتبيلة الجاميكية و البصل<br>الاحمر و الفلفل الرومي الأخضر و جبنة التشيدر<br>البيضاء 37</p>
  </article>

  <article class="menu-item" style="left:100px;top:640px;width:440px;">
    <h2 class="item-name">SPINACH FETA | <span class="ar">سبانخ وفيتا</span></h2>
    <p class="item-desc">Spinach, feta cheese, green bell peppers,<br>spring onions, and fresh dill&nbsp; 33</p>
    <p class="item-desc-ar">سبانخ، جبنة الفيتا، فلفل رومي أخضر،<br>بصل أخضر، شبت&nbsp; 33</p>
  </article>

  <article class="menu-item" style="left:100px;top:966px;width:440px;">
    <h2 class="item-name">TURKEY MELT | <span class="ar">تركي ميلت</span></h2>
    <p class="item-desc" style="margin-top:20px;">Turkey, swiss &amp; cheddar cheese, crushed<br>cumin, tomatos&nbsp; 44</p>
    <p class="item-desc-ar">شرائح الديك الرومي المدخن، جبنة سويسرية<br>وجبنة تشيدر، كمون وطماطم&nbsp; 44</p>
  </article>

  <div class="food-photo" role="img" aria-label="Photo of a steak and swiss turnover cut open beside fries" style="left:665px;top:974px;width:429px;height:284px;"></div>

  <div class="doodle-area" role="img" aria-label="Wavy line ornament" style="left:60px;top:1108px;width:40px;height:326px;"></div>
  <div class="doodle-area" role="img" aria-label="Line drawing of an eggplant" style="left:522px;top:1024px;width:70px;height:60px;"></div>
  <div class="doodle-area" role="img" aria-label="Line drawings of a bell pepper and a pea pod" style="left:186px;top:1178px;width:210px;height:76px;"></div>
  <div class="doodle-area" role="img" aria-label="Line drawing of a pear" style="left:590px;top:1132px;width:48px;height:58px;"></div>
  <div class="doodle-area" role="img" aria-label="Line drawing of a plum" style="left:544px;top:1256px;width:46px;height:60px;"></div>
  <div class="doodle-area" role="img" aria-label="Line drawings of a cutting board and a frying pan" style="left:536px;top:1424px;width:82px;height:160px;"></div>

  <article class="menu-item" style="left:100px;top:1296px;width:420px;">
    <h2 class="item-name">HALOUMI &amp; MINT<br>PESTO |<br><span class="ar">حلومي و بيستو النعناع</span></h2>
    <p class="item-desc" style="margin-top:14px;">Haloumi &amp; mozzarella cheese, mint pesto, olive<br>tapenade, tomatos&nbsp; 25</p>
    <p class="item-desc-ar">جبنة حلومي وموزاريلا، بيستو نعناع، خليط<br>الزيتون المبهر، طماطم&nbsp; 25</p>
  </article>

  <article class="menu-item" style="left:660px;top:1297px;width:420px;">
    <h2 class="item-name">STEAK &amp; SWISSS |<br><span class="ar">ستيك أند سويس</span></h2>
    <p class="item-desc" style="margin-top:34px;">Thinly sliced steak, mushrooms, onions, &amp;<br>swiss cheese sauce&nbsp; 37</p>
    <p class="item-desc-ar">شرائح اللحم البقري، فطر، بصل وصوص<br>الجبنة السويسرية&nbsp; 37</p>
  </article>

  <article class="menu-item" style="left:100px;top:1577px;width:420px;">
    <h2 class="item-name">SPICEY STEAK |<br><span class="ar">الستيك الحارق</span></h2>
    <p class="item-desc" style="margin-top:72px;">Thinly sliced steak, onions, green bell peppers,<br>hot sauce, and cheddar cheese&nbsp; 37</p>
    <p class="item-desc-ar">شرائح اللحم البقري، فلفل رومي أخضر، بصل<br>مع الشطة الحارقة و جبنة التشيدر البيضاء&nbsp; 37</p>
  </article>

  <article class="menu-item" style="left:676px;top:1577px;width:420px;">
    <h2 class="item-name">CHICKEN FAJITA |<br><span class="ar">دجاج الفاهيتا</span></h2>
    <p class="item-desc" style="margin-top:34px;">Fajita chicken strips, onions, red &amp; green<br>bell peppers, cheddar &amp; mozzarella cheese<br>37</p>
    <p class="item-desc-ar">شرائح دجاج الفاهيتا مع البصل والفلفل<br>الرومي الأخضر والأحمر مع جبنة التشيدر<br>والموزاريلا&nbsp; 37</p>
  </article>

  <div class="doodle-area" role="img" aria-label="Rolling pin ornament on the divider line" style="left:468px;top:2017px;width:284px;height:46px;"></div>

</main>
</body>
</html>
```